Business card for medical clinic

I need an upmarket, modern medical/health business card for my clinic

Contact Information for Business Card

name, address, email, qr code

```html
<!DOCTYPE html>
<html lang="en">
<head>
<meta charset="utf-8">
<title>Meridell Health Partners – Business Card</title>
<link href="https://fonts.googleapis.com/css2?family=Montserrat:wght@400;500;700&display=swap" rel="stylesheet">
<style>
  :root {
    --stage: #2b2c2e;
    --navy: #1b2a47;
    --navy-mid: #2d4b6e;
    --sky: #29a8e0;
    --sky-soft: #3bb2e6;
    --white: #ffffff;
    --paper: #f6f7f8;
    --paper-shade: #e9ebed;
    --divider-grey: #dcdfe2;
  }
  * { margin: 0; padding: 0; box-sizing: border-box; }
  html, body {
    width: 1200px; height: 960px; overflow: hidden;
    background: var(--stage);
    font-family: "Montserrat", Arial, sans-serif;
  }
  .canvas { position: relative; width: 1200px; height: 960px; }
  .card {
    position: absolute; left: 320px;
    width: 560px; height: 320px;
    border-radius: 16px; overflow: hidden;
    box-shadow: 0 14px 30px rgba(0,0,0,.45);
  }
  .card--front {
    top: 110px;
    background: linear-gradient(35deg, var(--sky) 0%, #3a8fbd 35%, var(--navy-mid) 62%, var(--navy) 100%);
  }
  .card--back { top: 530px; }
  .card svg.shapes { position: absolute; inset: 0; }

  .brand {
    position: absolute; left: 0; right: 0;
    text-align: center; color: var(--white);
    font-weight: 500; letter-spacing: 4px; text-transform: uppercase;
  }
  .card--front .brand { top: 128px; font-size: 30px; }
  .brand__rule {
    position: absolute; left: 110px; right: 110px; top: 178px;
    height: 2px; background: var(--white);
  }
  .site-link {
    position: absolute; bottom: 22px; left: 0; right: 0;
    display: flex; justify-content: center; align-items: center; gap: 8px;
    color: var(--white); font-size: 13px; letter-spacing: .5px;
  }

  .pattern-fill {
    position: absolute; inset: 0;
    background: linear-gradient(135deg, var(--paper) 0%, var(--paper-shade) 100%);
    clip-path: polygon(340px 0, 560px 0, 560px 320px, 500px 320px, 340px 176px);
  }
  .card--back .brand {
    left: 350px; right: 10px; top: 124px;
    font-size: 19px; letter-spacing: 2px; color: var(--navy-mid);
    font-weight: 500; line-height: 1.35;
  }
  .person { position: absolute; left: 80px; top: 40px; color: var(--white); }
  .person__name { font-size: 25px; font-weight: 700; letter-spacing: 1px; }
  .person__role { font-size: 14px; margin-top: 2px; }
  .contact-list {
    position: absolute; left: 80px; top: 118px;
    list-style: none; color: var(--white); font-size: 13px; line-height: 18px;
  }
  .contact-list li { margin-bottom: 14px; }
</style>
</head>
<body>
<div class="canvas">

  <section class="card card--front" aria-label="Card front">
    <div class="brand">Meridell Health<br><span style="font-size:15px;letter-spacing:8px">Partners</span></div>
    <div class="brand__rule"></div>
    <div class="site-link">
      <svg width="14" height="14" viewBox="0 0 14 14" fill="none" stroke="#fff" stroke-width="1.2">
        <circle cx="7" cy="7" r="6"/><ellipse cx="7" cy="7" rx="2.6" ry="6"/><line x1="1" y1="7" x2="13" y2="7"/>
      </svg>
      www.meridellhealth.com
    </div>
  </section>

  <section class="card card--back" aria-label="Card back">
    <svg class="shapes" width="560" height="320" viewBox="0 0 560 320">
      <defs>
        <linearGradient id="panelGradient" x1="0" y1="1" x2="1" y2="0">
          <stop offset="0" stop-color="#29a8e0"/>
          <stop offset=".45" stop-color="#2d5e88"/>
          <stop offset="1" stop-color="#1b2a47"/>
        </linearGradient>
      </defs>
      <rect class="panel" width="560" height="320" fill="url(#panelGradient)"/>
      <polygon class="accent-top" points="240,0 330,0 330,80" fill="#29a8e0"/>
      <polygon class="accent-bottom" points="385,222 520,320 385,320" fill="#3bb2e6"/>
      <polygon class="divider-grey" points="318,0 330,0 330,165 490,320 470,320 318,178" fill="#dcdfe2"/>
      <polygon class="divider-blue" points="332,0 340,0 340,176 504,320 494,320 332,180" fill="#29a8e0"/>
      <g class="icon-chain" fill="#fff" stroke="#fff">
        <line x1="50" y1="70" x2="50" y2="290" stroke-width="2"/>
        <polygon points="50,52 66,61 66,79 50,88 34,79 34,61" stroke="none"/>
        <circle cx="50" cy="66" r="4" fill="#29a8e0" stroke="none"/>
        <path d="M42 78 q8 -10 16 0 z" fill="#29a8e0" stroke="none"/>
        <g fill="#2b5f8c" stroke-width="2">
          <polygon points="50,124 66,133 66,151 50,160 34,151 34,133"/>
          <polygon points="50,192 66,201 66,219 50,228 34,219 34,201"/>
          <polygon points="50,256 66,265 66,283 50,292 34,283 34,265"/>
        </g>
        <path d="M44 138 h12 v8 h-12 z M42 138 q8 -6 16 0" fill="none" stroke-width="1.5"/>
        <rect x="43" y="205" width="14" height="10" fill="none" stroke-width="1.5"/>
        <polyline points="43,205 50,211 57,205" fill="none" stroke-width="1.5"/>
        <path d="M50 282 q-7 -8 -7 -12 a7 7 0 0 1 14 0 q0 4 -7 12 z" stroke="none"/>
        <circle cx="50" cy="270" r="2.5" fill="#2b5f8c" stroke="none"/>
      </g>
    </svg>
    <div class="pattern-fill" role="img" aria-label="Faint light grey triangle pattern background"></div>
    <div class="brand">Meridell Health<br><span style="font-size:12px;letter-spacing:5px">Partners</span></div>
    <div class="person">
      <div class="person__name">OWEN HARTLEY</div>
      <div class="person__role">Managing Director</div>
    </div>
    <ul class="contact-list">
      <li>555-014-2286<br>555-014-2291</li>
      <li>hello@meridellcare.com<br>www.meridellcare.com</li>
      <li>48 Larkfield Road,<br>Ashmont, WI 53500</li>
    </ul>
  </section>

</div>
</body>
</html>
```